RWT Fittings Ltd Business Cards

We need a business card with our business logo. We provide window and door installations on high-rises in west coast British Colombia, Canada.

I would like my business information and details on one side of the card, and the other side the company name with logo

Target Market(s)

General Contractors

Industry/Entity Type

Construction

Contact Information for Business Card

one side i want my company name and logo in the dark theme logo that i provided

Requirements
Must have
• Marco Peltieri, 16045518293, RWTFittings@mailbox-demo.com, 1407-5194 Linden Row Burnaby BC, V5H 2K9, Owner & Manager

```html
<!DOCTYPE html>
<html lang="en">
<head>
<meta charset="utf-8">
<title>RWT Fittings Ltd – Business Cards</title>
<link rel="stylesheet" href="https://fonts.googleapis.com/css2?family=Open+Sans:wght@400;600;700&display=swap">
<style>
  :root {
    --backdrop: #454545;
    --card-black: #151515;
    --card-white: #ffffff;
    --brand-blue: #29a8e0;
    --brand-grey: #8f8f8f;
    --text-light: #f2f2f2;
    --pattern-dark: #1c1c1c;
    --pattern-mid: #262626;
  }
  * { box-sizing: border-box; margin: 0; padding: 0; }
  html, body { width: 1200px; height: 780px; overflow: hidden; }
  body {
    background: var(--backdrop);
    font-family: "Open Sans", sans-serif;
    position: relative;
  }
  .card {
    position: absolute;
    top: 235px;
    width: 540px;
    height: 309px;
    overflow: hidden;
    background: var(--card-black);
    box-shadow: 0 10px 30px rgba(0,0,0,.45);
  }
  .card--front { left: 40px; }
  .card--back { left: 620px; }

  .front-shape { position: absolute; inset: 0; width: 540px; height: 309px; }

  .wordmark {
    position: absolute;
    display: flex;
    align-items: center;
    gap: 10px;
    color: var(--brand-blue);
    font-weight: 700;
    white-space: nowrap;
  }
  .wordmark__square { display: block; background: var(--brand-grey); }
  .card--front .wordmark { left: 236px; top: 58px; font-size: 28px; }
  .card--front .wordmark__square { width: 30px; height: 30px; }

  .holder { position: absolute; left: 28px; top: 162px; }
  .holder__name {
    color: var(--brand-blue);
    font-weight: 700;
    font-size: 16px;
    letter-spacing: .3px;
    text-transform: uppercase;
  }
  .holder__title { color: var(--text-light); font-size: 12px; margin-top: 2px; }

  .divider {
    position: absolute;
    left: 196px; top: 168px;
    width: 1px; height: 60px;
    background: var(--brand-blue);
  }

  .contacts { position: absolute; left: 210px; top: 186px; list-style: none; }
  .contacts li {
    display: flex; align-items: center; gap: 7px;
    color: var(--text-light); font-size: 11.5px; line-height: 20px;
  }
  .contacts svg { width: 11px; height: 11px; flex: none; }

  .address {
    position: absolute; left: 28px; top: 270px;
    color: var(--text-light); font-size: 11.5px;
  }

  .back-pattern {
    position: absolute; inset: 0;
    background: linear-gradient(135deg, var(--pattern-mid), var(--pattern-dark) 60%, var(--card-black));
  }
  .card--back .wordmark {
    left: 50%; top: 50%;
    transform: translate(-50%, -50%);
    font-size: 24px;
  }
  .card--back .wordmark__square { width: 24px; height: 24px; }
</style>
</head>
<body>

<section class="card card--front" aria-label="Card front, contact side">
  <svg class="front-shape" viewBox="0 0 540 309" aria-hidden="true">
    <path d="M150 0 Q200 170 540 215 V0 Z" fill="var(--card-white)"/>
    <path d="M162 12 Q214 182 540 228" fill="none" stroke="var(--brand-blue)" stroke-width="1.6"/>
  </svg>

  <div class="wordmark"><span class="wordmark__square"></span>RWT Fittings Ltd</div>

  <div class="holder">
    <p class="holder__name">Marco Peltieri</p>
    <p class="holder__title">Owner &amp; Manager</p>
  </div>

  <span class="divider"></span>

  <ul class="contacts">
    <li>
      <svg viewBox="0 0 12 12"><path d="M2.5 1 L4.5 1 L5.2 3.5 L4 4.5 Q5 7 7.5 8 L8.5 6.8 L11 7.5 L11 9.5 Q10 11 8.5 11 Q1 10 1 2.5 Q1 1 2.5 1 Z" fill="var(--brand-blue)"/></svg>
      16045518293
    </li>
    <li>
      <svg viewBox="0 0 12 12"><rect x="1" y="2.5" width="10" height="7" fill="var(--brand-blue)"/><path d="M1 2.5 L6 6.5 L11 2.5" fill="none" stroke="var(--card-black)" stroke-width="1"/></svg>
      RWTFittings@mailbox-demo.com
    </li>
    <li>
      <svg viewBox="0 0 12 12"><circle cx="6" cy="6" r="5" fill="var(--brand-blue)"/><path d="M1 6 H11 M6 1 Q3 6 6 11 M6 1 Q9 6 6 11" fill="none" stroke="var(--card-black)" stroke-width=".8"/></svg>
      www.rwtfittings-demo.com
    </li>
  </ul>

  <p class="address">1407-5194 Linden Row Burnaby BC, V5H 2K9</p>
</section>

<section class="card card--back" aria-label="Card back, company side">
  <div class="back-pattern" role="img" aria-label="Tonal dark pattern of repeated building shapes"></div>
  <div class="wordmark"><span class="wordmark__square"></span>RWT Fittings Ltd</div>
</section>

</body>
</html>
```